Pebble Tracks - explore habits of productive people

Pebble Tracks is a social place around habits and productivity

The full brief below:

https://notes.brimwellpad.net/page/d/7Qx-RtVmPLa93KwBz-H-cNmq2YeTsRfvUdGkHpXwaB/view?mode=shared

Colors

Designer to choose colors to be used in the design.

Requirements
Must have
• - a feed page to display habits
• - a habit page to add a habit
• / clean, no cluttered design, lots of white space
• / inspired by material design or other design system
Nice to have
• - user page

```html
<!DOCTYPE html>
<html lang="en">
<head>
<meta charset="utf-8">
<title>Pebble Tracks – Feeds</title>
<link href="https://fonts.googleapis.com/css2?family=Lato:wght@400;700&display=swap" rel="stylesheet">
<style>
  :root{
    --bar:#2f2f2f;
    --page:#efefef;
    --card:#ffffff;
    --ink:#2e2e2e;
    --muted:#444444;
    --blue:#1f63a8;
    --line:#d9d9d9;
    --field:#c9c9c9;
  }
  *{box-sizing:border-box;margin:0;padding:0}
  html,body{width:904px;height:1200px;overflow:hidden}
  body{background:var(--page);font-family:'Lato',sans-serif;color:var(--ink);position:relative}
  .topbar{position:absolute;left:0;top:0;width:904px;height:45px;background:var(--bar);color:#fff}
  .brand{position:absolute;left:19px;top:10px;font-size:18px;font-weight:700}
  .account{position:absolute;left:750px;top:11px;display:flex;align-items:center;gap:12px;font-size:10px;font-weight:700}
  .avatar{border-radius:50%;flex:none}
  .avatar.him{background:radial-gradient(circle at 50% 40%,#e3b89c 0 35%,#3a3a3a 36% 60%,#e9e9e9 61%)}
  .avatar.her{background:radial-gradient(circle at 50% 45%,#efc3a4 0 38%,#d9a868 39% 62%,#f2e6dc 63%)}
  .sidebar{position:absolute;left:20px;top:45px;width:148px;height:1085px;background:var(--card)}
  .nav{list-style:none;margin-top:13px}
  .nav li{height:32px;display:flex;align-items:center;gap:14px;padding-left:14px;font-size:9.5px;color:var(--blue);border-bottom:1px solid var(--line)}
  .nav li:last-child{border-bottom:none}
  .nav svg{width:9px;height:9px;fill:var(--blue)}
  .composer{position:absolute;left:181px;top:54px;width:542px;height:44px;background:var(--card);font-size:8.5px;padding:18px 0 0 11px}
  .post{position:absolute;left:181px;width:542px;height:331px;background:var(--card)}
  .post .avatar{position:absolute;left:17px;top:14px;width:43px;height:43px}
  .post .name{position:absolute;left:69px;top:21px;font-size:11.5px;font-weight:700;color:var(--blue)}
  .post .meta{position:absolute;left:69px;top:39px;font-size:8.5px;color:var(--muted)}
  .post .text{position:absolute;left:17px;top:67px;font-size:11px;font-weight:700}
  .stats{position:absolute;left:17px;top:96px;display:flex;gap:10px;font-size:8.5px;color:var(--blue)}
  .stats span{display:flex;align-items:center;gap:4px}
  .stats svg{width:9px;height:9px;fill:var(--blue)}
  .photo{position:absolute;left:15px;top:123px;width:480px;height:158px}
  .photo.coffee{background:linear-gradient(100deg,#6b5446,#b98a6a 35%,#efe6dc 55%,#4a3a30 85%)}
  .photo.yoga{background:linear-gradient(180deg,#7b7fa8,#d9a8b3 35%,#3d5873 55%,#2b3f4f)}
  .photo.todo{background:linear-gradient(110deg,#f2f2f2,#cfcfcf 55%,#d9a089 75%,#6f6f6f)}
  .comment{position:absolute;left:15px;top:290px;width:481px;height:27px;border:1px solid var(--field);font-size:8.5px;padding:8px 0 0 7px}
  .comment-tools{position:absolute;left:502px;top:298px;display:flex;gap:9px}
  .comment-tools svg{width:10px;height:10px}
  .aside{position:absolute;left:737px;top:45px;width:148px;height:1085px;background:var(--card)}
  .search{position:absolute;left:9px;top:10px;width:127px;height:26px;border:1.5px solid var(--field);font-size:9px;padding:7px 0 0 9px}
  .search svg{position:absolute;right:8px;top:7px;width:9px;height:9px}
  .aside h2{position:absolute;left:9px;font-size:12px;font-weight:700}
  .bday{position:absolute;left:9px;display:flex;gap:7px}
  .bday .avatar{width:28px;height:28px}
  .bday b{display:block;font-size:9px;font-weight:400;color:var(--blue);margin-top:1px}
  .bday i{font-style:normal;font-size:9px}
  .polls{position:absolute;left:9px;top:200px;width:130px;font-size:7.5px;line-height:12px}
  .polls p{margin-bottom:10px}
  .footer{position:absolute;left:0;top:1150px;width:904px;height:50px;background:var(--bar);color:#fff;font-size:8px;text-align:center;padding-top:21px}
</style>
</head>
<body>
  <header class="topbar">
    <div class="brand">Pebble Tracks</div>
    <div class="account"><div class="avatar him" role="img" aria-label="User profile photo" style="width:22px;height:22px"></div>Username</div>
  </header>

  <nav class="sidebar">
    <ul class="nav">
      <li><svg viewBox="0 0 10 10"><rect width="10" height="10" rx="1"/></svg>Feeds</li>
      <li><svg viewBox="0 0 10 10"><rect y="1" width="10" height="9" rx="1"/></svg>Planner</li>
      <li><svg viewBox="0 0 10 10"><circle cx="3" cy="3" r="2"/><circle cx="7" cy="3" r="2"/><rect y="6" width="10" height="4" rx="2"/></svg>Groups</li>
      <li><svg viewBox="0 0 10 10"><path d="M2 0h4l3 3v7H2z"/></svg>Documents</li>
      <li><svg viewBox="0 0 10 10"><path d="M5 5V0a5 5 0 1 1-5 5z"/></svg>Attendance</li>
      <li><svg viewBox="0 0 10 10"><rect x="1" y="1" width="8" height="6"/><rect y="8" width="10" height="1.5"/></svg>Quiz</li>
    </ul>
  </nav>

  <div class="composer">Write something here</div>

  <article class="post" style="top:106px">
    <div class="avatar her" role="img" aria-label="Author profile photo"></div>
    <div class="name">Name Heading</div>
    <div class="meta">3 hours &nbsp;I&nbsp; Mauris mauris enim</div>
    <p class="text">After I pour my morning cup of coffee, I will meditate for sixty seconds.</p>
    <div class="stats">
      <span><svg viewBox="0 0 10 10"><path d="M0 4h2v6H0zM3 4l3-4 1 1-1 3h4v3l-2 3H3z"/></svg>23</span>
      <span><svg viewBox="0 0 10 10"><path d="M0 0h2v6H0zM3 6l3 4 1-1-1-3h4V3L8 0H3z"/></svg>3</span>
      <span><svg viewBox="0 0 10 10"><ellipse cx="5" cy="4.5" rx="5" ry="4"/><path d="M1 10l1-3 2 1z"/></svg>230</span>
    </div>
    <div class="photo coffee" role="img" aria-label="Coffee being poured into pour-over filters"></div>
    <div class="comment">Add Comments</div>
    <div class="comment-tools">
      <svg viewBox="0 0 10 10"><path fill="#444" d="M0 5l10-5-3 10-2-4z"/></svg>
      <svg viewBox="0 0 10 10"><circle cx="5" cy="5" r="4.3" fill="none" stroke="#444"/><path d="M3 6q2 2 4 0" fill="none" stroke="#444"/></svg>
    </div>
  </article>

  <article class="post" style="top:452px">
    <div class="avatar her" role="img" aria-label="Author profile photo"></div>
    <div class="name">Name Heading</div>
    <div class="meta">3 hours &nbsp;I&nbsp; Mauris mauris enim</div>
    <p class="text">After I meditate for sixty seconds, I will write my to-do list for the day.</p>
    <div class="stats">
      <span><svg viewBox="0 0 10 10"><path d="M0 4h2v6H0zM3 4l3-4 1 1-1 3h4v3l-2 3H3z"/></svg>23</span>
      <span><svg viewBox="0 0 10 10"><path d="M0 0h2v6H0zM3 6l3 4 1-1-1-3h4V3L8 0H3z"/></svg>3</span>
      <span><svg viewBox="0 0 10 10"><ellipse cx="5" cy="4.5" rx="5" ry="4"/><path d="M1 10l1-3 2 1z"/></svg>230</span>
    </div>
    <div class="photo yoga" role="img" aria-label="Person meditating by the sea at sunset"></div>
    <div class="comment">Add Comments</div>
    <div class="comment-tools">
      <svg viewBox="0 0 10 10"><path fill="#444" d="M0 5l10-5-3 10-2-4z"/></svg>
      <svg viewBox="0 0 10 10"><circle cx="5" cy="5" r="4.3" fill="none" stroke="#444"/><path d="M3 6q2 2 4 0" fill="none" stroke="#444"/></svg>
    </div>
  </article>

  <article class="post" style="top:798px">
    <div class="avatar her" role="img" aria-label="Author profile photo"></div>
    <div class="name">Name Heading</div>
    <div class="meta">3 hours &nbsp;I&nbsp; Mauris mauris enim</div>
    <p class="text">After I write my to-do list for the day, I will immediately begin my first task.</p>
    <div class="stats">
      <span><svg viewBox="0 0 10 10"><path d="M0 4h2v6H0zM3 4l3-4 1 1-1 3h4v3l-2 3H3z"/></svg>23</span>
      <span><svg viewBox="0 0 10 10"><path d="M0 0h2v6H0zM3 6l3 4 1-1-1-3h4V3L8 0H3z"/></svg>3</span>
      <span><svg viewBox="0 0 10 10"><ellipse cx="5" cy="4.5" rx="5" ry="4"/><path d="M1 10l1-3 2 1z"/></svg>230</span>
    </div>
    <div class="photo todo" role="img" aria-label="Hand writing a to-do list in a notebook"></div>
    <div class="comment">Add Comments</div>
    <div class="comment-tools">
      <svg viewBox="0 0 10 10"><path fill="#444" d="M0 5l10-5-3 10-2-4z"/></svg>
      <svg viewBox="0 0 10 10"><circle cx="5" cy="5" r="4.3" fill="none" stroke="#444"/><path d="M3 6q2 2 4 0" fill="none" stroke="#444"/></svg>
    </div>
  </article>

  <aside class="aside">
    <div class="search">Search<svg viewBox="0 0 10 10"><circle cx="4" cy="4" r="3" fill="none" stroke="#333" stroke-width="1.5"/><path d="M6.3 6.3L9.5 9.5" stroke="#333" stroke-width="1.6"/></svg></div>
    <h2 style="top:55px">Birthdays</h2>
    <div class="bday" style="top:82px"><div class="avatar her" role="img" aria-label="Friend profile photo"></div><div><b>Name Heading</b><i>3 hours</i></div></div>
    <div class="bday" style="top:122px"><div class="avatar him" role="img" aria-label="Friend profile photo"></div><div><b>Name Heading</b><i>3 hours</i></div></div>
    <h2 style="top:177px">My Result Polls</h2>
    <div class="polls">
      <p>Lorem ipsum dolor sit amet, con-sectetur adipiscing elit.</p>
      <p>Lorem ipsum dolor sit amet, con-sectetur adipiscing elit.</p>
      <p>Lorem ipsum dolor sit amet, con-sectetur adipiscing elit.</p>
      <p>Lorem ipsum dolor sit amet, con-sectetur adipiscing elit.</p>
    </div>
  </aside>

  <footer class="footer">Copyright © 2018. Company Name. &nbsp; All Right Reserved</footer>
</body>
</html>
```